Lanternfield Drinks business cards

We need a business card design for our new logo. The company is modern, progressive, professional, yet approachable. The key products are ready to drink bottles and cans of coffee based beverages.
These cards will be a critical part of the first impression made by our sales organization, business development team, and all external facing personnel.
Card can be a vertical or horizontal orientation.

Target Market(s)

Customers, suppliers, business partners

Industry/Entity Type

Business

Contact Information for Business Card

Business cards should feature Company Name and Logo.

Font styles to use
Serif

Colors

Designer to choose colors to be used in the design.

Requirements
Must have
• Strong readability of Name, phone #, mobile number and email address.
• Job title, website url, Street Address, and other details can be secondary level readability.
Nice to have
• High impact, simplistic quality design.
• Ok to utilize the 'H in the box' separate from the company name

```html
<!DOCTYPE html>
<html lang="en">
<head>
<meta charset="UTF-8">
<title>Lanternfield Drinks – Business Cards</title>
<link rel="stylesheet" href="https://fonts.googleapis.com/css2?family=Cinzel:wght@700&family=Lato:wght@400;700&display=swap">
<style>
  :root {
    --backdrop: #2b2522;
    --card: #050505;
    --orange: #f0582a;
    --amber: #f5a21c;
    --white: #ffffff;
    --rule: #4a4a4a;
    --pattern: #1c1c1c;
  }
  * { box-sizing: border-box; margin: 0; padding: 0; }
  html, body { width: 1200px; height: 844px; overflow: hidden; background: var(--backdrop); }
  .canvas { position: relative; width: 1200px; height: 844px; }
  .card {
    position: absolute; top: 268px; width: 540px; height: 308px;
    background: var(--card); overflow: hidden;
    box-shadow: 0 10px 24px rgba(0,0,0,.5);
  }
  .card--front { left: 40px; }
  .card--back { left: 620px; }

  .brand { position: absolute; left: 36px; top: 48px; display: flex; align-items: center; gap: 18px; }
  .brand__square { width: 62px; height: 62px; border: 5px solid var(--orange); }
  .brand__name {
    font-family: "Cinzel", Georgia, serif; font-weight: 700; font-size: 30px;
    color: var(--orange); letter-spacing: 1px; line-height: 1;
  }
  .rule { position: absolute; height: 1px; background: var(--rule); }
  .rule--top { left: 200px; right: 36px; top: 140px; }
  .rule--bottom { left: 36px; right: 250px; top: 200px; }

  .contact {
    position: absolute; right: 36px; top: 152px; list-style: none;
    font-family: "Lato", Arial, sans-serif; font-size: 13.5px; color: var(--white);
    text-align: right; line-height: 19px;
  }
  .contact li { display: flex; justify-content: flex-end; align-items: center; gap: 8px; }
  .contact svg { width: 11px; height: 11px; fill: var(--orange); flex: none; }

  .person { position: absolute; left: 36px; top: 212px; font-family: "Lato", Arial, sans-serif; }
  .person__name { font-weight: 700; font-size: 21px; color: var(--orange); line-height: 24px; }
  .person__title { font-size: 14px; color: var(--amber); line-height: 18px; }
  .person__address { font-size: 14px; color: var(--white); line-height: 18px; font-style: normal; }

  .back__pattern { position: absolute; inset: 0; background: linear-gradient(160deg, var(--pattern), #121212 70%, var(--card)); }
  .back__mark {
    position: absolute; left: 50%; top: 50%; transform: translate(-50%, -50%);
    display: flex; align-items: center; gap: 14px; padding: 26px 28px;
    background: var(--card); border: 5px solid var(--orange);
  }
  .back__square { width: 18px; height: 18px; background: var(--orange); }
  .back__name {
    font-family: "Cinzel", Georgia, serif; font-weight: 700; font-size: 24px;
    color: var(--orange); letter-spacing: 1px; line-height: 1;
  }
</style>
</head>
<body>
<main class="canvas">
  <section class="card card--front" aria-label="Business card front">
    <div class="brand">
      <div class="brand__square"></div>
      <div class="brand__name">Lanternfield Drinks</div>
    </div>
    <div class="rule rule--top"></div>
    <ul class="contact">
      <li>312 408 7719
        <svg viewBox="0 0 24 24"><path d="M6.6 10.8a15 15 0 0 0 6.6 6.6l2.2-2.2a1 1 0 0 1 1-.25 11.4 11.4 0 0 0 3.6.57 1 1 0 0 1 1 1V20a1 1 0 0 1-1 1A17 17 0 0 1 3 4a1 1 0 0 1 1-1h3.5a1 1 0 0 1 1 1c0 1.25.2 2.45.57 3.57a1 1 0 0 1-.25 1z"/></svg></li>
      <li>312 408 7720
        <svg viewBox="0 0 24 24"><path d="M7 1h10a2 2 0 0 1 2 2v18a2 2 0 0 1-2 2H7a2 2 0 0 1-2-2V3a2 2 0 0 1 2-2zm0 3v15h10V4z"/></svg></li>
      <li>hello@lanternfield.co
        <svg viewBox="0 0 24 24"><path d="M2 4h20v16H2zm2 2v.5l8 5 8-5V6z"/></svg></li>
      <li>www.lanternfield.co
        <svg viewBox="0 0 24 24"><circle cx="12" cy="12" r="10"/></svg></li>
    </ul>
    <div class="rule rule--bottom"></div>
    <div class="person">
      <p class="person__name">DANA WHITLOW</p>
      <p class="person__title">Managing Director</p>
      <address class="person__address">18 Kettle Row,<br>Brookmere, 60417<br>United States</address>
    </div>
  </section>

  <section class="card card--back" aria-label="Business card back">
    <div class="back__pattern" role="img" aria-label="Repeated company name as a faint dark background pattern"></div>
    <div class="back__mark">
      <div class="back__square"></div>
      <div class="back__name">Lanternfield Drinks</div>
    </div>
  </section>
</main>
</body>
</html>
```